BLS Business Card 2018

Larkmere Chiropractic. We have two locations that we want to advertise on the same card. Brightvale OrthoCore campus address: 3815 Pellham Dr., Suite 240, Flowood, MS 39417. Madison address: 246 Willowmere Dr., Building D., Madison, MS 39284. website: www.drlarkmere-example.com. o:(601)555-0147 f:(601)555-0183

Target Market(s)

Health care decision makers: primary care doctors and mothers

Contact Information for Business Card

I have no idea; up for any suggestions and I'd do much better picking from examples versus describing what I'm looking for. We are in a very high end location and would like the cards to look really sharp.

Requirements
Must have
• My name, Martin R Belvane, D.C.

```html
<!DOCTYPE html>
<html lang="en">
<head>
<meta charset="utf-8">
<title>Larkmere Chiropractic – Business Card</title>
<link href="https://fonts.googleapis.com/css2?family=Cinzel:wght@400&family=Open+Sans:wght@400;700&display=swap" rel="stylesheet">
<style>
  :root {
    --backdrop: #e9e7e4;
    --card-black: #000000;
    --card-white: #ffffff;
    --brand-blue: #1c4f96;
    --ink: #111111;
    --paper-text: #f4f4f4;
  }
  * { box-sizing: border-box; margin: 0; padding: 0; }
  html, body { width: 1200px; height: 900px; overflow: hidden; }
  body {
    background: var(--backdrop);
    position: relative;
    font-family: "Open Sans", Arial, sans-serif;
  }
  .card {
    position: absolute;
    width: 612px;
    height: 364px;
    overflow: hidden;
    box-shadow: 0 4px 14px rgba(0,0,0,0.18);
  }

  /* Front */
  .card-front { left: 175px; top: 45px; background: var(--card-black); color: var(--paper-text); }
  .front-artwork {
    position: absolute; left: 0; top: 0; width: 318px; height: 100%;
    background: linear-gradient(100deg, var(--brand-blue) 0%, var(--brand-blue) 35%, #e8ecf3 62%, #ffffff 100%);
    clip-path: polygon(0 0, 100% 0, 82% 100%, 0 100%);
  }
  .doctor-name {
    position: absolute; left: 314px; top: 90px;
    font-family: "Cinzel", Georgia, serif; font-size: 19px; letter-spacing: 0.5px;
  }
  .contact-lines {
    position: absolute; left: 314px; top: 131px;
    font-size: 15px; line-height: 22px; list-style: none;
  }
  .front-brand {
    position: absolute; left: 300px; top: 252px;
    display: flex; align-items: center; gap: 12px;
    font-family: "Cinzel", Georgia, serif; font-weight: 400; color: var(--paper-text);
  }
  .front-brand .brand-dot { width: 40px; height: 40px; border-radius: 50%; border: 1.5px solid var(--paper-text); }
  .front-brand .brand-name { font-size: 28px; line-height: 28px; }
  .front-brand .brand-sub { font-size: 19px; line-height: 22px; display: block; }

  /* Back */
  .card-back { left: 541px; top: 476px; background: var(--card-white); color: var(--ink); text-align: center; }
  .back-brand {
    position: absolute; left: 90px; top: 70px;
    display: flex; align-items: center; gap: 16px; text-align: left;
    font-family: "Cinzel", Georgia, serif; font-weight: 400; color: var(--ink);
  }
  .back-brand .brand-dot { width: 60px; height: 60px; border-radius: 50%; border: 1.5px solid var(--ink); }
  .back-brand .brand-name { font-size: 42px; line-height: 44px; }
  .back-brand .brand-sub { font-size: 28px; line-height: 30px; display: block; }
  .locations { position: absolute; left: 0; right: 0; top: 226px; font-size: 15px; line-height: 22px; }
  .location + .location { margin-top: 10px; }
  .location-name { font-weight: 700; text-transform: uppercase; }
</style>
</head>
<body>

<section class="card card-front">
  <div class="front-artwork" role="img" aria-label="Illustration of an athletic figure reaching upward, in white on a blue panel"></div>
  <h1 class="doctor-name">MARTIN R BELVANE, D.C.</h1>
  <ul class="contact-lines">
    <li>P: (601)555-0147</li>
    <li>F: (601)555-0183</li>
    <li>www.drlarkmere-example.com</li>
  </ul>
  <div class="front-brand">
    <span class="brand-dot"></span>
    <span><span class="brand-name">LARKMERE</span><span class="brand-sub">CHIROPRACTIC</span></span>
  </div>
</section>

<section class="card card-back">
  <div class="back-brand">
    <span class="brand-dot"></span>
    <span><span class="brand-name">LARKMERE</span><span class="brand-sub">CHIROPRACTIC</span></span>
  </div>
  <div class="locations">
    <div class="location">
      <p class="location-name">Brightvale OrthoCore Campus</p>
      <p>3815 Pellham Dr., Suite 240 Flowood, MS 39417.</p>
    </div>
    <div class="location">
      <p class="location-name">Madison</p>
      <p>246 Willowmere Dr., Building D., Madison, MS 39284.</p>
    </div>
  </div>
</section>

</body>
</html>
```